7K packaging design

We are a wholesaler for Automotive Spare Parts in Jordan and Iraq market and we needs to import spare parts from China under our company private brand "7K"
The 7K brand’s product lines include Filtration, Braking Systems, Wheels, Wheel Bolts & Nuts, Shock Absorbers, Sensors, Cooling Systems, Axles and more.
The aim of the project is to unify the brand packaging across all the product lines , we will start by the brake pads then based on the approved design we will do the other products

Target Market(s)

Jordan , Iraq Market

Industry/Entity Type

Automotive spare parts

Requirements
Must have
• Name of the product :Ceramic brake pads specs : Superior stopping power Noise suppression Low Dust Technology Made in china
Nice to have
• Brake pad outline image on the box
Should not have
• Blue color

```html
<!DOCTYPE html>
<html lang="en">
<head>
<meta charset="utf-8">
<title>7K packaging design – Ceramic Brake Pads dieline</title>
<link rel="stylesheet" href="https://fonts.googleapis.com/css2?family=Exo+2:ital,wght@0,800;1,800&family=Roboto+Condensed:wght@500;700&display=swap">
<style>
  :root {
    --charcoal: #333333;
    --red-bright: #ff0a14;
    --red-mid: #d4000c;
    --red-dark: #9a0008;
    --red-deep: #4a0006;
    --grey-light: #bdbdbd;
    --grey-mid: #8a8a8a;
    --grey-dark: #4b4b4b;
    --silver: #e6e6e6;
    --dieline: #3cc4d8;
    --white: #ffffff;
  }
  html, body {
    margin: 0;
    padding: 0;
    width: 1200px;
    height: 660px;
    overflow: hidden;
    background: var(--white);
  }
  .artboard { display: block; width: 1200px; height: 660px; }
  .panel-dark { fill: var(--charcoal); }
  .cut-line { fill: none; stroke: var(--dieline); stroke-width: 1.5; }
  .panel-edge { stroke: var(--dieline); stroke-width: 1.5; }
  .dust-flap { fill: url(#redUp); stroke: var(--dieline); stroke-width: 1.5; }
  .silver-stripe { fill: var(--silver); }
  .feature-band { fill: url(#bandGrey); }
  .pad-art-area { fill: url(#padGlow); }
  .photo-area { fill: url(#photoGrey); }
  .product-title {
    font-family: "Exo 2", sans-serif;
    font-style: italic;
    font-weight: 800;
    fill: var(--white);
  }
  .brand-name {
    font-family: "Exo 2", sans-serif;
    font-style: normal;
    font-weight: 800;
    fill: var(--white);
  }
  .feature-text {
    font-family: "Roboto Condensed", sans-serif;
    font-weight: 700;
    font-size: 9px;
    fill: var(--white);
  }
  .origin-text {
    font-family: "Roboto Condensed", sans-serif;
    font-weight: 700;
    font-size: 13px;
    fill: var(--white);
  }
  .icon-line { fill: none; stroke: var(--white); stroke-width: 2; }
  .icon-fill { fill: var(--white); }
</style>
</head>
<body>
<svg class="artboard" viewBox="0 0 2560 1408" xmlns="http://www.w3.org/2000/svg" role="img" aria-label="7K Ceramic Brake Pads box dielines, two variants">
  <defs>
    <linearGradient id="redDown" x1="0" y1="0" x2="0" y2="1">
      <stop offset="0" style="stop-color:var(--red-deep)"/>
      <stop offset=".75" style="stop-color:var(--red-bright)"/>
      <stop offset="1" style="stop-color:var(--red-bright)"/>
    </linearGradient>
    <linearGradient id="redUp" x1="0" y1="0" x2=".3" y2="1">
      <stop offset="0" style="stop-color:var(--red-bright)"/>
      <stop offset=".55" style="stop-color:var(--red-mid)"/>
      <stop offset="1" style="stop-color:var(--red-deep)"/>
    </linearGradient>
    <linearGradient id="redFront" x1="0" y1="0" x2="1" y2="1">
      <stop offset="0" style="stop-color:var(--red-bright)"/>
      <stop offset=".6" style="stop-color:var(--red-bright)"/>
      <stop offset="1" style="stop-color:var(--red-mid)"/>
    </linearGradient>
    <linearGradient id="redDiag" x1="0" y1="0" x2="1" y2="1">
      <stop offset="0" style="stop-color:var(--red-deep)"/>
      <stop offset=".6" style="stop-color:var(--red-mid)"/>
      <stop offset="1" style="stop-color:var(--red-bright)"/>
    </linearGradient>
    <radialGradient id="padGlow" cx=".5" cy=".5" r=".5">
      <stop offset="0" style="stop-color:var(--red-dark);stop-opacity:.55"/>
      <stop offset="1" style="stop-color:var(--red-dark);stop-opacity:0"/>
    </radialGradient>
    <linearGradient id="bandGrey" x1="0" y1="0" x2="1" y2="0">
      <stop offset="0" style="stop-color:var(--grey-mid)"/>
      <stop offset="1" style="stop-color:var(--grey-light)"/>
    </linearGradient>
    <linearGradient id="photoGrey" x1="0" y1="0" x2="1" y2="1">
      <stop offset="0" style="stop-color:var(--grey-light)"/>
      <stop offset=".5" style="stop-color:var(--grey-mid)"/>
      <stop offset="1" style="stop-color:var(--grey-dark)"/>
    </linearGradient>

    <g id="features">
      <circle class="icon-fill" cx="13" cy="0" r="12"/>
      <circle cx="13" cy="0" r="7" style="fill:var(--red-mid)"/>
      <circle class="icon-fill" cx="13" cy="0" r="3"/>
      <text class="feature-text" x="32"><tspan x="32" y="-7">SUPERIOR</tspan><tspan x="32" y="3">STOPPING</tspan><tspan x="32" y="13">POWER</tspan></text>
      <path class="icon-line" d="M88 -5 h6 l8 -7 v24 l-8 -7 h-6 z M106 -6 l6 -4 M107 0 h7 M106 6 l6 4"/>
      <text class="feature-text" x="120"><tspan x="120" y="-2">NOISE</tspan><tspan x="120" y="8">SUPPRESSION</tspan></text>
      <circle class="icon-line" cx="190" cy="0" r="11" stroke-dasharray="4 3"/>
      <circle class="icon-fill" cx="186" cy="-3" r="2"/>
      <circle class="icon-fill" cx="194" cy="3" r="2"/>
      <text class="feature-text" x="208"><tspan x="208" y="-2">LOW DUST</tspan><tspan x="208" y="8">TECHNOLOGY</tspan></text>
    </g>

    <g id="dieline">
      <!-- top flaps -->
      <rect class="panel-dark panel-edge" x="70" y="72" width="278" height="238"/>
      <rect class="panel-edge" x="348" y="72" width="590" height="238" fill="url(#redDown)"/>
      <rect class="panel-dark panel-edge" x="938" y="72" width="277" height="238"/>

      <!-- back panel and dust flaps -->
      <rect class="panel-dark panel-edge" x="70" y="350" width="278" height="240"/>
      <rect class="panel-edge" x="348" y="310" width="590" height="280" fill="url(#redDown)"/>
      <rect class="panel-dark panel-edge" x="938" y="350" width="277" height="240"/>
      <path class="cut-line" d="M160 590 v-17 h100 v17 M1028 590 v-17 h100 v17"/>

      <!-- top panel -->
      <rect class="panel-edge" x="348" y="590" width="590" height="238" fill="var(--red-mid)"/>
      <polygon points="348,635 722,635 630,828 348,828" fill="url(#redDiag)"/>
      <polygon class="feature-band" points="348,590 742,590 722,635 348,635"/>
      <rect class="pad-art-area" role="img" aria-label="White line drawing of a pair of brake pads" x="365" y="640" width="265" height="180"/>
      <use href="#features" transform="translate(676 612) rotate(180)"/>

      <!-- front panel -->
      <rect x="70" y="828" width="278" height="227" fill="url(#redUp)"/>
      <rect x="348" y="828" width="590" height="277" fill="url(#redFront)"/>
      <rect x="938" y="828" width="277" height="227" fill="url(#redUp)"/>
      <path class="cut-line" d="M70 828 V1055 H155 v12 h107 v-12 H348 M938 1055 H1023 v12 h107 v-12 H1215 V828 M348 828 V1105 M938 828 V1105"/>
      <rect class="pad-art-area" role="img" aria-label="White line drawing of a pair of brake pads" x="615" y="865" width="300" height="205"/>
      <text class="brand-name" x="437" y="915" font-size="64" text-anchor="middle">7K</text>
      <text class="product-title" x="375" y="999" font-size="27">Ceramic Brake Pads</text>
      <use href="#features" transform="translate(375 1055)"/>

      <!-- bottom panel and side wings -->
      <path class="dust-flap" d="M348 1105 H185 Q135 1105 137 1160 Q150 1290 250 1335 Q270 1345 300 1345 H348 Z"/>
      <path class="dust-flap" d="M938 1105 H1100 Q1150 1105 1148 1160 Q1135 1290 1035 1335 Q1015 1345 985 1345 H938 Z"/>
      <rect class="panel-edge" x="348" y="1105" width="590" height="240" fill="var(--red-mid)"/>
      <polygon points="662,1105 938,1105 938,1300 570,1300" fill="url(#redDiag)"/>
      <polygon class="feature-band" points="570,1300 938,1300 938,1345 548,1345"/>
      <rect class="pad-art-area" role="img" aria-label="White line drawing of a pair of brake pads" x="655" y="1115" width="265" height="180"/>
      <use href="#features" transform="translate(608 1322) scale(1.05)"/>
    </g>
  </defs>

  <!-- Variant A -->
  <g class="dieline-variant">
    <use href="#dieline"/>
    <rect class="photo-area" role="img" aria-label="Greyscale photo of a truck front" x="70" y="590" width="278" height="238"/>
    <polygon class="photo-area" role="img" aria-label="Greyscale photo of a truck front" points="744,590 938,590 938,828 642,828"/>
    <rect class="photo-area" role="img" aria-label="Greyscale photo of a truck front" x="938" y="590" width="277" height="238"/>
    <polygon class="photo-area" role="img" aria-label="Greyscale photo of a truck front" points="348,1105 658,1105 566,1300 544,1345 348,1345"/>
  </g>

  <!-- Variant B -->
  <g class="dieline-variant" transform="translate(1289 0)">
    <use href="#dieline"/>
    <rect class="photo-area" role="img" aria-label="Greyscale photo of a race car" x="70" y="590" width="278" height="238"/>
    <polygon class="photo-area" role="img" aria-label="Greyscale photo of a race car" points="744,590 938,590 938,828 642,828"/>
    <rect class="photo-area" role="img" aria-label="Greyscale photo of a race car" x="938" y="590" width="277" height="238"/>
    <polygon class="photo-area" role="img" aria-label="Greyscale photo of a race car" points="348,1105 658,1105 566,1300 544,1345 348,1345"/>
  </g>

  <!-- shared text on the photo areas, both variants -->
  <g id="overlay">
    <polygon class="silver-stripe" points="722,590 744,590 642,828 620,828"/>
    <polygon class="silver-stripe" points="644,1105 662,1105 556,1345 538,1345"/>
    <text class="product-title" transform="translate(918 667) rotate(180)" font-size="26"><tspan x="0" y="0">Ceramic</tspan><tspan x="0" y="22">Brake</tspan><tspan x="0" y="44">Pads</tspan></text>
    <text class="brand-name" transform="translate(868 760) rotate(180)" font-size="48" text-anchor="middle">7K</text>
    <text class="origin-text" transform="translate(1077 606) rotate(180)" text-anchor="middle">MADE IN CHINA</text>
    <text class="product-title" transform="translate(1186 634) rotate(180)" font-size="21">Ceramic Brake Pads</text>
    <text class="brand-name" transform="translate(1075 735) rotate(180)" font-size="76" text-anchor="middle">7K</text>
    <text class="brand-name" x="414" y="1177" font-size="56" text-anchor="middle">7K</text>
    <text class="product-title" font-size="30"><tspan x="367" y="1265">Ceramic</tspan><tspan x="367" y="1288">Brake</tspan><tspan x="367" y="1311">Pads</tspan></text>
  </g>
  <use href="#overlay" transform="translate(1289 0)"/>
</svg>
</body>
</html>
```